Compnay PowerPoint Tempalte Design

I am needing a good base design and slide designs for interior and exterior company presentations. The template will need to be on the company brand with proper coloring and fonts. Able to be creative with layout options with a good example attached.
website for reference: www.crewvlt.com/

Target Market(s)

Professionals

Font styles to use
Other font styles liked:
• Helvetica

Requirements
Must have
• On Brand Colors, Clean, simple design

```html
<!DOCTYPE html>
<html lang="en">
<head>
<meta charset="utf-8">
<title>CREWVLT Presentation Template</title>
<link href="https://fonts.googleapis.com/css2?family=Arimo:wght@400;700&display=swap" rel="stylesheet">
<style>
:root{
  --teal:#3aa597;
  --teal-dark:#1f7a72;
  --blue:#1688b5;
  --ink:#24282d;
  --grey:#6b6f74;
  --pale:#a9d9d2;
  --canvas:#d9d9db;
  --stage:#e6e8eb;
  --grad-teal:linear-gradient(90deg,#3ca997 0%,#2a9aa5 50%,#1588b6 100%);
  --grad-dark:linear-gradient(90deg,#23272c 0%,#1f4f60 45%,#1588b6 100%);
}
*{box-sizing:border-box;margin:0;padding:0}
html,body{width:1200px;height:3750px;overflow:hidden}
body{background:var(--canvas);font-family:"Arimo",Helvetica,Arial,sans-serif;color:var(--ink);position:relative}
.stage{position:absolute;left:0;top:0;width:1200px;height:700px;background:var(--stage)}
.hero{position:absolute;left:178px;top:113px;transform:scale(1.5);transform-origin:0 0;box-shadow:0 8px 30px rgba(0,0,0,.18)}
.slide{position:absolute;width:562px;height:316px;background:#fff;overflow:hidden}
.col-a{left:28px}.col-b{left:609px}.col-c{left:319px}
.brand{font-weight:700;color:var(--ink);letter-spacing:.5px}
/* title slides */
.title-slide{background:var(--grad-teal)}
.title-slide.dark{background:var(--grad-dark)}
.title-head{position:absolute;left:0;top:0}
.title-url{position:absolute;left:48px;top:22px;font-size:6.5px;color:var(--grey);line-height:1.3;max-width:300px}
.title-brand{position:absolute;right:38px;top:74px;font-size:20px}
.title-main{position:absolute;left:48px;top:118px;color:var(--ink)}
.title-slide.dark .title-main{color:#fff}
.title-main h1{font-size:31px;font-weight:700;line-height:1}
.title-main h2{font-size:30px;font-weight:400;line-height:1.1}
.title-main p{font-size:15px;margin-top:8px}
.title-main time{display:block;font-size:7px;margin-top:30px}
.title-foot{position:absolute;left:0;bottom:0;width:100%;height:11px;background:#333538;color:#fff;font-size:4.5px;text-align:center;line-height:11px}
/* content slide footer */
.slide-foot{position:absolute;left:10px;right:10px;bottom:6px;height:20px}
.foot-brand{position:absolute;left:0;bottom:0;font-size:9px;font-weight:700;color:var(--ink)}
.foot-bar{position:absolute;left:54px;right:0;bottom:2px;height:7px;background:var(--grad-teal);display:flex;justify-content:flex-end;gap:14px;padding-right:8px;color:#fff;font-size:3.5px;line-height:7px}
.s-title{position:absolute;left:0;width:100%;text-align:center;font-size:21px;font-weight:700;color:var(--ink)}
.s-title span{font-weight:400}
.lorem{font-size:6.3px;line-height:1.25;color:var(--grey)}
.t-teal{color:var(--teal);font-weight:700}
.photo{position:absolute;background:linear-gradient(135deg,#b79a7c,#8d7563 60%,#5f6e78)}
.photo-frame{position:absolute;border:2px solid var(--teal)}
.band-teal{position:absolute;left:0;top:0;width:100%;background:var(--grad-teal)}
.icon{display:inline-flex;align-items:center;justify-content:center;width:22px;height:22px;border-radius:50%;background:var(--teal);flex:none}
.icon.blue{background:var(--blue)}
.icon i{width:8px;height:8px;border:2px solid #fff;border-radius:50%}
/* toc */
.toc{position:absolute;left:68px;top:100px;display:grid;grid-template-columns:222px 222px;row-gap:16px}
.toc-item{display:flex;gap:10px}
.toc-item b{font-size:18px;color:#b5b8bb;font-weight:400;width:12px}
.toc-item h3{font-size:11px;color:var(--teal);font-weight:400}
/* columns */
.cols4{position:absolute;left:30px;right:30px;display:grid;grid-template-columns:repeat(4,1fr);gap:14px;text-align:center}
.cols4 h3{font-size:10px;color:var(--teal);margin-bottom:5px}
.list8{position:absolute;left:62px;top:95px;display:grid;grid-template-columns:225px 225px;row-gap:12px}
.list8 .row{display:flex;gap:8px;align-items:flex-start}
.list8 h3{font-size:8.5px;color:var(--teal);font-weight:400;margin-bottom:2px}
.list8 .lorem{font-size:5.3px}
table{border-collapse:collapse}
.data-table{position:absolute;left:25px;top:85px;width:512px;font-size:6.3px}
.data-table th{background:var(--teal);color:#fff;height:14px;font-weight:700;text-align:center}
.data-table th:first-child{text-align:left;padding-left:4px;background:var(--teal-dark)}
.data-table td{height:16px;text-align:center;color:var(--ink);border-bottom:1px solid #fff}
.data-table tr:nth-child(odd) td{background:#e9f3f2}
.data-table td:first-child{text-align:left;padding-left:4px}
.mini-table{position:absolute;left:288px;top:112px;width:250px;font-size:5.5px}
.mini-table th{background:var(--teal);color:#fff;height:11px}
.mini-table th:first-child{background:var(--ink);text-align:left;padding-left:3px}
.mini-table td{height:11px;text-align:center;border-bottom:1px solid #e4e4e4}
.mini-table td:first-child{text-align:left;padding-left:3px}
.contact{position:absolute;left:58px;top:118px;color:#fff}
.contact .brand{color:#fff;font-size:24px}
.contact h3{font-size:12px;margin:14px 0 10px}
.contact li{list-style:none;display:flex;align-items:center;gap:8px;font-size:7.5px;margin-bottom:7px}
</style>
</head>
<body>

<div class="stage">
  <section class="slide title-slide dark hero">
    <svg class="title-head" width="562" height="120" viewBox="0 0 562 120"><polygon points="0,0 562,0 562,112 450,112 412,64 0,64" fill="#fff"/><polygon points="0,67 410,67 448,115 562,115 562,119 446,119 408,71 0,71" fill="#a9d9d2"/></svg>
    <p class="title-url">https://www.crewvlt.com</p>
    <div class="title-brand brand">CREWVLT</div>
    <div class="title-main"><h1>PRESENTATION</h1><h2>Title Goes Here!</h2><p>Subtitle of Presentation Goes Here!</p><time>September 27, 2021</time></div>
    <div class="title-foot">Copyright 2021 CREWVLT. All rights reserved</div>
  </section>
</div>

<!-- row 1 -->
<section class="slide title-slide col-a" style="top:727px">
  <svg class="title-head" width="562" height="120" viewBox="0 0 562 120"><polygon points="0,0 562,0 562,112 450,112 412,64 0,64" fill="#fff"/><polygon points="0,67 410,67 448,115 562,115 562,119 446,119 408,71 0,71" fill="#a9d9d2"/></svg>
  <p class="title-url">https://www.crewvlt.com</p>
  <div class="title-brand brand">CREWVLT</div>
  <div class="title-main"><h1>PRESENTATION</h1><h2>Title Goes Here!</h2><p>Subtitle of Presentation Goes Here!</p><time>September 27, 2021</time></div>
  <div class="title-foot">Copyright 2021 CREWVLT. All rights reserved</div>
</section>
<section class="slide title-slide dark col-b" style="top:727px">
  <svg class="title-head" width="562" height="120" viewBox="0 0 562 120"><polygon points="0,0 562,0 562,112 450,112 412,64 0,64" fill="#fff"/><polygon points="0,67 410,67 448,115 562,115 562,119 446,119 408,71 0,71" fill="#a9d9d2"/></svg>
  <p class="title-url">https://www.crewvlt.com</p>
  <div class="title-brand brand">CREWVLT</div>
  <div class="title-main"><h1>PRESENTATION</h1><h2>Title Goes Here!</h2><p>Subtitle of Presentation Goes Here!</p><time>September 27, 2021</time></div>
  <div class="title-foot">Copyright 2021 CREWVLT. All rights reserved</div>
</section>

<!-- row 2 -->
<section class="slide title-slide col-a" style="top:1062px">
  <svg class="title-head" width="562" height="120" viewBox="0 0 562 120"><polygon points="0,0 562,0 562,112 450,112 412,64 0,64" fill="#fff"/><polygon points="0,67 410,67 448,115 562,115 562,119 446,119 408,71 0,71" fill="#a9d9d2"/></svg>
  <p class="title-url">Lorem ipsum dolor sit amet, consectetur adipiscing elit. Vivamus eu dui ex. Curabitur dapibus dignissim dui, in molestie metus.</p>
  <div class="title-brand brand">CREWVLT</div>
  <div class="title-main"><h1>PRESENTATION</h1><h2>Title Goes Here!</h2><p>Subtitle of Presentation Goes Here!</p><time>September 27, 2021</time></div>
  <div class="title-foot">Copyright 2021 CREWVLT. All rights reserved</div>
</section>
<section class="slide title-slide dark col-b" style="top:1062px">
  <svg class="title-head" width="562" height="120" viewBox="0 0 562 120"><polygon points="0,0 562,0 562,112 450,112 412,64 0,64" fill="#fff"/><polygon points="0,67 410,67 448,115 562,115 562,119 446,119 408,71 0,71" fill="#a9d9d2"/></svg>
  <p class="title-url">Lorem ipsum dolor sit amet, consectetur adipiscing elit. Vivamus eu dui ex. Curabitur dapibus dignissim dui, in molestie metus.</p>
  <div class="title-brand brand">CREWVLT</div>
  <div class="title-main"><h1>PRESENTATION</h1><h2>Title Goes Here!</h2><p>Subtitle of Presentation Goes Here!</p><time>September 27, 2021</time></div>
  <div class="title-foot">Copyright 2021 CREWVLT. All rights reserved</div>
</section>

<!-- row 3 -->
<section class="slide col-a" style="top:1397px">
  <h2 class="s-title" style="top:46px;font-weight:400">Table of <b>Contents</b></h2>
  <div class="toc">
    <div class="toc-item"><b>1</b><div><h3>Title Goes Here!</h3><p class="lorem">Lorem ipsum dolor sit amet, consectetur<br>adipiscing elit. Vivamus eu dui ex.</p></div></div>
    <div class="toc-item"><b>2</b><div><h3>Title Goes Here!</h3><p class="lorem">Lorem ipsum dolor sit amet, consectetur<br>adipiscing elit. Vivamus eu dui ex.</p></div></div>
    <div class="toc-item"><b>3</b><div><h3><strong>Title</strong> Goes Here!</h3><p class="lorem">Lorem ipsum dolor sit amet, consectetur<br>adipiscing elit. Vivamus eu dui ex.</p></div></div>
    <div class="toc-item"><b>4</b><div><h3>Title Goes Here!</h3><p class="lorem">Lorem ipsum dolor sit amet, consectetur<br>adipiscing elit. Vivamus eu dui ex.</p></div></div>
    <div class="toc-item"><b>5</b><div><h3>Title Goes Here!</h3><p class="lorem">Lorem ipsum dolor sit amet, consectetur<br>adipiscing elit. Vivamus eu dui ex.</p></div></div>
    <div class="toc-item"><b>6</b><div><h3>Title Goes Here!</h3><p class="lorem">Lorem ipsum dolor sit amet, consectetur<br>adipiscing elit. Vivamus eu dui ex.</p></div></div>
  </div>
  <div class="slide-foot"><span class="foot-brand">CREWVLT</span><div class="foot-bar"><span>Copyright 2021 CREWVLT. All rights reserved</span><span>5</span></div></div>
</section>
<section class="slide col-b" style="top:1397px">
  <h2 style="position:absolute;left:42px;top:92px;font-size:21px;font-weight:400">About <b>Us</b></h2>
  <p class="lorem" style="position:absolute;left:42px;top:124px;width:200px;font-size:7px">Lorem ipsum dolor sit amet, consectetur adipiscing elit. Vivamus eu dui ex. Curabitur dapibus dignissim dui, in molestie metus feugiat sed. Praesent aliquet lorem ex, eu dapibus odio varius at. Duis eget tellus porta, consequat lacus vitae, venenatis dolor. Nulla facilisi. In et sollicitudin lacus. Donec risus orci, gravida sit amet risus vehicula, aliquet pretium sapien. Nullam sit amet magna non ex bibendum mollis. Nunc vel neque eu augue dignissim congue.</p>
  <div class="photo-frame" style="left:258px;top:58px;width:262px;height:172px"></div>
  <div class="photo" role="img" aria-label="Photo of a team working together over documents and a laptop" style="left:266px;top:66px;width:248px;height:156px"></div>
  <div class="slide-foot"><span class="foot-brand">CREWVLT</span><div class="foot-bar"><span>Copyright 2021 CREWVLT. All rights reserved</span><span>6</span></div></div>
</section>

<!-- row 4 -->
<section class="slide col-a" style="top:1732px">
  <div class="photo-frame" style="left:40px;top:42px;width:226px;height:108px"></div>
  <div class="photo" role="img" aria-label="Photo of colleagues joining hands over a desk" style="left:48px;top:34px;width:214px;height:104px"></div>
  <div class="photo-frame" style="left:298px;top:42px;width:226px;height:108px"></div>
  <div class="photo" role="img" aria-label="Top view photo of a team meeting at a wooden table" style="left:306px;top:34px;width:214px;height:104px;background:linear-gradient(135deg,#8a6a4c,#b58f68 55%,#6a7f8a)"></div>
  <div style="position:absolute;left:44px;top:190px;width:220px"><h3 style="font-size:16px">Title Goes Here!</h3><p class="lorem" style="font-size:7px;margin-top:6px">Lorem ipsum dolor sit amet, consectetur adipiscing elit. Vivamus eu dui ex. Curabitur dapibus dignissim dui, in molestie metus feugiat sed. Praesent aliquet lorem ex, eu dapibus odio varius at.</p></div>
  <div style="position:absolute;left:300px;top:190px;width:220px"><h3 style="font-size:16px">Title Goes Here!</h3><p class="lorem" style="font-size:7px;margin-top:6px">Lorem ipsum dolor sit amet, consectetur adipiscing elit. Vivamus eu dui ex. Curabitur dapibus dignissim dui, in molestie metus feugiat sed. Praesent aliquet lorem ex, eu dapibus odio varius at.</p></div>
  <div class="slide-foot"><span class="foot-brand">CREWVLT</span><div class="foot-bar"><span>Copyright 2021 CREWVLT. All rights reserved</span><span>7</span></div></div>
</section>
<section class="slide col-b" style="top:1732px">
  <div class="band-teal" style="height:132px"></div>
  <h2 class="s-title" style="top:48px;color:#fff;font-weight:400">Meet The <b>Team</b></h2>
  <div class="cols4" style="grid-template-columns:repeat(3,1fr);top:96px;left:70px;right:70px;gap:40px">
    <div><div role="img" aria-label="Portrait photo of team member" style="width:76px;height:76px;border-radius:50%;margin:0 auto 10px;background:#cfd3d6;border:3px solid #fff;box-shadow:0 0 0 1px #ddd"></div><h3 style="margin-bottom:2px">Person Name</h3><p class="lorem" style="color:var(--ink);margin-bottom:6px">Job Title Goes Here!</p><p class="lorem">Lorem ipsum dolor sit amet, consectetur adipiscing elit. Vivamus eu dui ex. Curabitur dapibus dignissim dui, in molestie metus feugiat sed.</p></div>
    <div><div role="img" aria-label="Portrait photo of team member" style="width:76px;height:76px;border-radius:50%;margin:0 auto 10px;background:#cfd3d6;border:3px solid #fff;box-shadow:0 0 0 1px #ddd"></div><h3 style="margin-bottom:2px">Person Name</h3><p class="lorem" style="color:var(--ink);margin-bottom:6px">Job Title Goes Here!</p><p class="lorem">Lorem ipsum dolor sit amet, consectetur adipiscing elit. Vivamus eu dui ex. Curabitur dapibus dignissim dui, in molestie metus feugiat sed.</p></div>
    <div><div role="img" aria-label="Portrait photo of team member" style="width:76px;height:76px;border-radius:50%;margin:0 auto 10px;background:#cfd3d6;border:3px solid #fff;box-shadow:0 0 0 1px #ddd"></div><h3 style="margin-bottom:2px">Person Name</h3><p class="lorem" style="color:var(--ink);margin-bottom:6px">Job Title Goes Here!</p><p class="lorem">Lorem ipsum dolor sit amet, consectetur adipiscing elit. Vivamus eu dui ex. Curabitur dapibus dignissim dui, in molestie metus feugiat sed.</p></div>
  </div>
  <div class="slide-foot"><span class="foot-brand">CREWVLT</span><div class="foot-bar"><span>Copyright 2021 CREWVLT. All rights reserved</span><span>8</span></div></div>
</section>

<!-- row 5 -->
<section class="slide col-a" style="top:2067px">
  <div class="band-teal" style="height:156px"></div>
  <h2 class="s-title" style="top:48px;color:#fff;font-weight:400">Slide Title <span>Goes Here</span></h2>
  <p class="lorem" style="position:absolute;left:60px;right:60px;top:92px;text-align:center;color:#fff;font-size:8px">Lorem ipsum dolor sit amet, consectetur adipiscing elit. Vivamus eu dui ex. Curabitur dapibus dignissim dui, in molestie metus feugiat sed. Praesent aliquet lorem ex, eu dapibus odio varius at.</p>
  <div class="cols4" style="top:172px">
    <div><h3>Title Goes Here</h3><p class="lorem">Lorem ipsum dolor sit amet, consectetur adipiscing elit. Vivamus eu dui ex. Curabitur dapibus dignissim dui, in molestie metus feugiat sed. Praesent aliquet lorem ex, eu dapibus odio varius at.</p></div>
    <div><h3>Title Goes Here</h3><p class="lorem">Lorem ipsum dolor sit amet, consectetur adipiscing elit. Vivamus eu dui ex. Curabitur dapibus dignissim dui, in molestie metus feugiat sed. Praesent aliquet lorem ex, eu dapibus odio varius at.</p></div>
    <div><h3>Title Goes Here</h3><p class="lorem">Lorem ipsum dolor sit amet, consectetur adipiscing elit. Vivamus eu dui ex. Curabitur dapibus dignissim dui, in molestie metus feugiat sed. Praesent aliquet lorem ex, eu dapibus odio varius at.</p></div>
    <div><h3>Title Goes Here</h3><p class="lorem">Lorem ipsum dolor sit amet, consectetur adipiscing elit. Vivamus eu dui ex. Curabitur dapibus dignissim dui, in molestie metus feugiat sed. Praesent aliquet lorem ex, eu dapibus odio varius at.</p></div>
  </div>
  <div class="slide-foot"><span class="foot-brand">CREWVLT</span><div class="foot-bar"><span>Copyright 2021 CREWVLT. All rights reserved</span><span>9</span></div></div>
</section>
<section class="slide col-b" style="top:2067px">
  <h2 class="s-title" style="top:46px">Slide Title <span>Goes Here!</span></h2>
  <div class="list8">
    <div class="row"><span class="icon"><i></i></span><div><h3>Title Goes Here!</h3><p class="lorem">Lorem ipsum dolor sit amet, consectetur adipiscing<br>elit. Vivamus eu dui ex. Curabitur dapibus.</p></div></div>
    <div class="row"><span class="icon blue"><i></i></span><div><h3>Title Goes Here!</h3><p class="lorem">Lorem ipsum dolor sit amet, consectetur adipiscing<br>elit. Vivamus eu dui ex. Curabitur dapibus.</p></div></div>
    <div class="row"><span class="icon" style="background:var(--ink)"><i></i></span><div><h3>Title Goes Here!</h3><p class="lorem">Lorem ipsum dolor sit amet, consectetur adipiscing<br>elit. Vivamus eu dui ex. Curabitur dapibus.</p></div></div>
    <div class="row"><span class="icon"><i></i></span><div><h3>Title Goes Here!</h3><p class="lorem">Lorem ipsum dolor sit amet, consectetur adipiscing<br>elit. Vivamus eu dui ex. Curabitur dapibus.</p></div></div>
    <div class="row"><span class="icon blue"><i></i></span><div><h3>Title Goes Here!</h3><p class="lorem">Lorem ipsum dolor sit amet, consectetur adipiscing<br>elit. Vivamus eu dui ex. Curabitur dapibus.</p></div></div>
    <div class="row"><span class="icon" style="background:var(--ink)"><i></i></span><div><h3>Title Goes Here!</h3><p class="lorem">Lorem ipsum dolor sit amet, consectetur adipiscing<br>elit. Vivamus eu dui ex. Curabitur dapibus.</p></div></div>
    <div class="row"><span class="icon"><i></i></span><div><h3>Title Goes Here!</h3><p class="lorem">Lorem ipsum dolor sit amet, consectetur adipiscing<br>elit. Vivamus eu dui ex. Curabitur dapibus.</p></div></div>
    <div class="row"><span class="icon blue"><i></i></span><div><h3>Title Goes Here!</h3><p class="lorem">Lorem ipsum dolor sit amet, consectetur adipiscing<br>elit. Vivamus eu dui ex. Curabitur dapibus.</p></div></div>
  </div>
  <div class="slide-foot"><span class="foot-brand">CREWVLT</span><div class="foot-bar"><span>Copyright 2021 CREWVLT. All rights reserved</span><span>10</span></div></div>
</section>

<!-- row 6 -->
<section class="slide col-a" style="top:2402px;background:var(--grad-dark)">
  <h2 style="position:absolute;left:50px;top:176px;font-size:30px;color:#fff">Section Break</h2>
  <p style="position:absolute;left:50px;top:222px;width:280px;font-size:10.5px;line-height:1.2;color:#fff">Lorem ipsum dolor sit amet, consectetur adipiscing elit. Vivamus eu dui ex. Curabitur dapibus dignissim dui, in molestie metus.</p>
</section>
<section class="slide col-b" style="top:2402px">
  <h2 class="s-title" style="top:46px">Slide Title <span>Goes Here!</span></h2>
  <svg style="position:absolute;left:200px;top:105px" width="160" height="140" viewBox="0 0 160 140">
    <polygon points="80,0 104,38 56,38" fill="#7fc7bb"/><polygon points="104,38 80,44 56,38 80,0" fill="#5fb8aa" opacity=".6"/>
    <polygon points="52,44 108,44 128,78 32,78" fill="#1688b5"/><polygon points="80,50 108,44 128,78 80,86" fill="#127aa3"/>
    <polygon points="28,84 132,84 156,124 4,124" fill="#3aa597"/><polygon points="80,94 132,84 156,124 80,138" fill="#1f7a72"/>
  </svg>
  <span class="icon" style="position:absolute;left:170px;top:153px;background:#fff;border:1.5px solid var(--blue)"><i style="border-color:var(--blue)"></i></span>
  <span class="icon" style="position:absolute;left:363px;top:100px"><i></i></span>
  <span class="icon" style="position:absolute;left:363px;top:205px;background:var(--teal-dark)"><i></i></span>
  <div style="position:absolute;left:50px;top:146px;width:110px;text-align:center"><h3 style="font-size:9px" class="t-teal">Title Goes Here!</h3><p class="lorem" style="font-size:5.5px;margin-top:3px">Lorem ipsum dolor sit amet, consectetur adipiscing elit. Vivamus eu dui ex. Curabitur dapibus dignissim dui, in molestie metus feugiat sed.</p></div>
  <div style="position:absolute;left:398px;top:93px;width:110px"><h3 style="font-size:9px;font-weight:400;color:var(--teal)">Title Goes Here!</h3><p class="lorem" style="font-size:5.5px;margin-top:3px">Lorem ipsum dolor sit amet, consectetur adipiscing elit. Vivamus eu dui ex. Curabitur dapibus dignissim dui, in molestie metus feugiat sed.</p></div>
  <div style="position:absolute;left:398px;top:200px;width:110px"><h3 style="font-size:9px;font-weight:400;color:var(--teal-dark)">Title Goes Here!</h3><p class="lorem" style="font-size:5.5px;margin-top:3px">Lorem ipsum dolor sit amet, consectetur adipiscing elit. Vivamus eu dui ex. Curabitur dapibus dignissim dui, in molestie metus feugiat sed.</p></div>
  <div class="slide-foot"><span class="foot-brand">CREWVLT</span><div class="foot-bar"><span>Copyright 2021 CREWVLT. All rights reserved</span><span>12</span></div></div>
</section>

<!-- row 7 -->
<section class="slide col-a" style="top:2737px">
  <h2 class="s-title" style="top:48px;font-weight:400">Our <b>Process</b></h2>
  <svg style="position:absolute;left:20px;top:120px" width="520" height="10" viewBox="0 0 520 10"><line x1="0" y1="5" x2="508" y2="5" stroke="#b8bcbf" stroke-width="1.2" stroke-dasharray="2 2"/><polygon points="508,1 516,5 508,9" fill="#b8bcbf"/></svg>
  <div class="cols4" style="top:107px;left:50px;right:50px;gap:40px">
    <div><div style="width:34px;height:34px;border-radius:50%;background:var(--teal);color:#fff;font-size:16px;font-weight:700;line-height:34px;margin:0 auto 10px">1</div><h3 style="font-size:10.5px">Title Goes<br>Here!</h3><p class="lorem">Lorem ipsum dolor sit amet, consectetur adipiscing elit. Vivamus eu dui ex. Curabitur dapibus dignissim dui, in molestie metus.</p></div>
    <div><div style="width:34px;height:34px;border-radius:50%;background:var(--blue);color:#fff;font-size:16px;font-weight:700;line-height:34px;margin:0 auto 10px">2</div><h3 style="font-size:10.5px;color:var(--blue)">Title Goes<br>Here!</h3><p class="lorem">Lorem ipsum dolor sit amet, consectetur adipiscing elit. Vivamus eu dui ex. Curabitur dapibus dignissim dui, in molestie metus.</p></div>
    <div><div style="width:34px;height:34px;border-radius:50%;background:var(--teal);color:#fff;font-size:16px;font-weight:700;line-height:34px;margin:0 auto 10px">3</div><h3 style="font-size:10.5px">Title Goes<br>Here!</h3><p class="lorem">Lorem ipsum dolor sit amet, consectetur adipiscing elit. Vivamus eu dui ex. Curabitur dapibus dignissim dui, in molestie metus.</p></div>
    <div><div style="width:34px;height:34px;border-radius:50%;background:var(--blue);color:#fff;font-size:16px;font-weight:700;line-height:34px;margin:0 auto 10px">4</div><h3 style="font-size:10.5px;color:var(--blue)">Title Goes<br>Here!</h3><p class="lorem">Lorem ipsum dolor sit amet, consectetur adipiscing elit. Vivamus eu dui ex. Curabitur dapibus dignissim dui, in molestie metus.</p></div>
  </div>
  <div class="slide-foot"><span class="foot-brand">CREWVLT</span><div class="foot-bar"><span>Copyright 2021 CREWVLT. All rights reserved</span><span>13</span></div></div>
</section>
<section class="slide col-b" style="top:2737px">
  <div class="band-teal" style="height:156px"></div>
  <h2 class="s-title" style="top:48px;color:#fff">Slide Title <span>Goes Here</span></h2>
  <p class="lorem" style="position:absolute;left:60px;right:60px;top:88px;text-align:center;color:#fff;font-size:8px">Lorem ipsum dolor sit amet, consectetur adipiscing elit. Vivamus eu dui ex. Curabitur dapibus dignissim dui, in molestie metus feugiat sed. Praesent aliquet lorem ex, eu dapibus odio varius at.</p>
  <div class="cols4" style="top:138px">
    <div><span class="icon" style="width:38px;height:38px;border:4px solid #fff;margin-bottom:6px"><i></i></span><h3>Title Goes Here</h3><p class="lorem">Lorem ipsum dolor sit amet, consectetur adipiscing elit. Vivamus eu dui ex. Curabitur dapibus dignissim dui, in molestie metus feugiat sed.</p></div>
    <div><span class="icon blue" style="width:38px;height:38px;border:4px solid #fff;margin-bottom:6px"><i></i></span><h3>Title Goes Here</h3><p class="lorem">Lorem ipsum dolor sit amet, consectetur adipiscing elit. Vivamus eu dui ex. Curabitur dapibus dignissim dui, in molestie metus feugiat sed.</p></div>
    <div><span class="icon" style="width:38px;height:38px;border:4px solid #fff;margin-bottom:6px"><i></i></span><h3>Title Goes Here</h3><p class="lorem">Lorem ipsum dolor sit amet, consectetur adipiscing elit. Vivamus eu dui ex. Curabitur dapibus dignissim dui, in molestie metus feugiat sed.</p></div>
    <div><span class="icon blue" style="width:38px;height:38px;border:4px solid #fff;margin-bottom:6px"><i></i></span><h3>Title Goes Here</h3><p class="lorem">Lorem ipsum dolor sit amet, consectetur adipiscing elit. Vivamus eu dui ex. Curabitur dapibus dignissim dui, in molestie metus feugiat sed.</p></div>
  </div>
  <div class="slide-foot"><span class="foot-brand">CREWVLT</span><div class="foot-bar"><span>Copyright 2021 CREWVLT. All rights reserved</span><span>14</span></div></div>
</section>

<!-- row 8 -->
<section class="slide col-a" style="top:3072px">
  <h2 class="s-title" style="top:46px;font-weight:400">Chart <b>Slide</b></h2>
  <svg style="position:absolute;left:40px;top:100px" width="250" height="170" viewBox="0 0 250 170" font-size="5" fill="#777">
    <g stroke="#e2e2e2" stroke-width=".6"><line x1="20" y1="10" x2="240" y2="10"/><line x1="20" y1="32" x2="240" y2="32"/><line x1="20" y1="54" x2="240" y2="54"/><line x1="20" y1="76" x2="240" y2="76"/><line x1="20" y1="98" x2="240" y2="98"/><line x1="20" y1="120" x2="240" y2="120"/><line x1="20" y1="142" x2="240" y2="142"/></g>
    <text x="10" y="12">6</text><text x="10" y="34">5</text><text x="10" y="56">4</text><text x="10" y="78">3</text><text x="10" y="100">2</text><text x="10" y="122">1</text><text x="10" y="144">0</text>
    <g fill="#3aa597"><rect x="28" y="47" width="7" height="95"/><rect x="64" y="87" width="7" height="55"/><rect x="100" y="65" width="7" height="77"/><rect x="136" y="43" width="7" height="99"/><rect x="172" y="47" width="7" height="95"/><rect x="208" y="87" width="7" height="55"/></g>
    <g fill="#1688b5"><rect x="36" y="89" width="7" height="53"/><rect x="72" y="45" width="7" height="97"/><rect x="108" y="102" width="7" height="40"/><rect x="144" y="80" width="7" height="62"/><rect x="180" y="89" width="7" height="53"/><rect x="216" y="45" width="7" height="97"/></g>
    <g fill="#1f6f6a"><rect x="44" y="98" width="7" height="44"/><rect x="80" y="98" width="7" height="44"/><rect x="116" y="76" width="7" height="66"/><rect x="152" y="32" width="7" height="110"/><rect x="188" y="98" width="7" height="44"/><rect x="224" y="98" width="7" height="44"/></g>
    <text x="26" y="152">Category 1</text><text x="62" y="152">Category 2</text><text x="98" y="152">Category 3</text><text x="134" y="152">Category 4</text><text x="170" y="152">Category 5</text><text x="206" y="152">Category 6</text>
  </svg>
  <p class="lorem" style="position:absolute;left:288px;top:82px;width:250px;font-size:5.5px">Lorem ipsum dolor sit amet, at laboris nibh duis mauris. Per ultrices lectus sed metus tristique eu. Diam suspendisse ac ipsum maecenas fermentum, aliquet imperdiet et lobortis venenatis nascetur luctus. A ac, vivamus erat nullam.</p>
  <table class="mini-table">
    <tr><th>Category</th><th>Series 1</th><th style="background:var(--blue)">Series 2</th><th style="background:var(--teal-dark)">Series 3</th></tr>
    <tr><td>Category 1</td><td>4.3</td><td>2.4</td><td>2</td></tr>
    <tr><td>Category 2</td><td>2.5</td><td>4.4</td><td>2</td></tr>
    <tr><td>Category 3</td><td>3.5</td><td>1.8</td><td>3</td></tr>
    <tr><td>Category 4</td><td>4.5</td><td>2.8</td><td>5</td></tr>
    <tr><td>Category 5</td><td>4.3</td><td>2.4</td><td>2</td></tr>
    <tr><td>Category 6</td><td>2.5</td><td>4.4</td><td>2</td></tr>
  </table>
  <div class="slide-foot"><span class="foot-brand">CREWVLT</span><div class="foot-bar"><span>Copyright 2021 CREWVLT. All rights reserved</span><span>15</span></div></div>
</section>
<section class="slide col-b" style="top:3072px">
  <h2 class="s-title" style="top:46px;font-weight:400">Table <b>Slide</b></h2>
  <table class="data-table">
    <tr><th>Heading</th><th>Title 1</th><th>Title 2</th><th>Title 3</th><th>Title 4</th><th>Title 5</th></tr>
    <tr><td>Lorem ipsum dolor sit amet</td><td>12</td><td>12</td><td>43</td><td>87</td><td>34</td></tr>
    <tr><td>Lorem ipsum dolor sit amet</td><td>45</td><td>34</td><td>34</td><td>12</td><td>55</td></tr>
    <tr><td>Lorem ipsum dolor sit amet</td><td>66</td><td>56</td><td>67</td><td>34</td><td>67</td></tr>
    <tr><td>Lorem ipsum dolor sit amet</td><td>78</td><td>90</td><td>23</td><td>56</td><td>12</td></tr>
    <tr><td>Lorem ipsum dolor sit amet</td><td>65</td><td>98</td><td>45</td><td>77</td><td>34</td></tr>
    <tr><td>Lorem ipsum dolor sit amet</td><td>23</td><td>67</td><td>55</td><td>87</td><td>11</td></tr>
    <tr><td>Lorem ipsum dolor sit amet</td><td>44</td><td>55</td><td>67</td><td>66</td><td>89</td></tr>
  </table>
  <div class="slide-foot"><span class="foot-brand">CREWVLT</span><div class="foot-bar"><span>Copyright 2021 CREWVLT. All rights reserved</span><span>16</span></div></div>
</section>

<!-- closing -->
<section class="slide col-c" style="top:3407px;background:var(--grad-dark)">
  <div class="contact">
    <div class="brand">CREWVLT</div>
    <h3>Contact Us</h3>
    <ul>
      <li><svg width="9" height="9" viewBox="0 0 10 10"><path d="M2 1l2 2-1 1.5c.6 1.2 1.3 1.9 2.5 2.5L7 6l2 2-1.5 1.5C4 9 1 6 .5 2.5z" fill="#fff"/></svg>555-0142-7788</li>
      <li><svg width="9" height="9" viewBox="0 0 10 10"><circle cx="5" cy="5" r="4" fill="none" stroke="#fff" stroke-width="1.2"/><circle cx="5" cy="5" r="1.6" fill="none" stroke="#fff" stroke-width="1"/></svg>info@crewvlt.com</li>
      <li><svg width="9" height="9" viewBox="0 0 10 10"><circle cx="5" cy="5" r="4" fill="none" stroke="#fff" stroke-width="1"/><ellipse cx="5" cy="5" rx="1.8" ry="4" fill="none" stroke="#fff" stroke-width=".8"/><line x1="1" y1="5" x2="9" y2="5" stroke="#fff" stroke-width=".8"/></svg>www.crewvlt.com</li>
    </ul>
  </div>
  <div class="title-foot">Copyright 2021 CREWVLT. All rights reserved</div>
</section>

</body>
</html>
```